Retail Package for Ammunition Company

We are looking for a packaging design for a retail boxed ammunition. The "look". Attached will be the logo to be used. The logo is attached and a can be manipulated on the box. Box to represent strength and accuracy. Will need to provide .psd files to allow in house personnel to add/remove text to other calibers and warnings. Wow me with your designs!

Browse Other Brands: http://www.brightfalconsupply.com/brands

The packaging needs to include:
Logo- provided and the following text:

FRONT 1. 9mm 115gr FMJ

BACK 2. WARNING: To avoid serious injury: (1) use only ammunition in good condition; use only in modern firearms in good condition marked for .22 Long Rifle (LR) cartridges; (2) always be sure barrel is free of any obstructions; the barrel should be checked in case of light recoil, or an unusually loud or weak sound heard during firing; (3) wear eye and ear protection; (4) if gun fails to fire, avoid exposure to breech when unloading and point muzzle in a safe direction. Keep firearm pointed in safe direction at all times; (5) discharge may occur if rim is struck; handle with caution, do not drop. (6) Do not shoot at hard surfaces or water to prevent ricochet; (7) Bullet is capable of traveling extreme distances. Know your backstop; (8) Store in cool dry place

3. LEAD WARNING: Discharging firearms in poorly ventilated areas, cleaning firearms, or handling ammunition may result in exposure to lead and other substances known to cause birth defects, reproductive harm, and other serious physical injury. Have adequate ventilation at all times. Wash hands thoroughly after exposure.

Dimensions ; (LxWxH): 5.25" x 2.625" x 1.125"

Target Market(s)

Ammunition Industry

```html
<!DOCTYPE html>
<html lang="en">
<head>
<meta charset="utf-8">
<title>Crimson Ridge Arms – 9mm 115gr FMJ Retail Box</title>
<link rel="stylesheet" href="https://fonts.googleapis.com/css2?family=Montserrat:wght@400;600;700;800&family=Open+Sans:wght@400;600;700&display=swap">
<style>
  :root{
    --bg:#ececec;
    --red-deep:#5e0406;
    --red:#8e1014;
    --red-bright:#c8232a;
    --brand-red:#8a1a1d;
    --white:#ffffff;
    --chrome-dark:#6b6b6b;
    --chrome-light:#d9d9d9;
    --ink:#111111;
    --text-light:#f3dede;
  }
  *{box-sizing:border-box;margin:0;padding:0}
  html,body{width:1200px;height:750px;overflow:hidden;background:var(--bg)}
  .canvas{position:relative;width:1200px;height:750px}
  .box-layout{position:absolute;left:78px;top:68px;width:1044px;height:614px}

  /* top panel */
  .top-panel{position:absolute;left:184px;top:0;width:860px;height:184px;
    background:linear-gradient(180deg,var(--red-deep) 0%,var(--red) 55%,#a5141a 100%);
    display:flex;flex-direction:column;align-items:center;justify-content:center;gap:10px;color:var(--white)}
  .top-panel .brand{color:var(--white)}
  .top-panel .product-line{font-family:"Montserrat",sans-serif;font-weight:700;font-size:15px;letter-spacing:1.5px;text-align:center;line-height:1.35}

  /* brand lockup */
  .brand{display:flex;align-items:center;gap:10px;font-family:"Montserrat",sans-serif;font-weight:800;font-size:30px;letter-spacing:1px;color:var(--brand-red);text-transform:uppercase}
  .brand-dot{width:26px;height:26px;border-radius:50%;background:currentColor}

  /* end panel */
  .end-panel{position:absolute;left:0;top:184px;width:184px;height:430px;overflow:hidden;
    background:linear-gradient(180deg,#8c1a1e 0%,var(--red-bright) 35%,#a2161c 65%)}
  .end-panel .brand{position:absolute;top:90px;left:0;width:100%;flex-direction:column;font-size:17px;text-align:center;color:var(--white);gap:12px;line-height:1.2}
  .end-panel .brand-dot{width:40px;height:40px}
  .end-chrome{position:absolute;left:0;top:272px;width:100%;height:18px;
    background:linear-gradient(180deg,var(--chrome-light),var(--chrome-dark) 50%,var(--chrome-light))}
  .end-label{position:absolute;left:0;top:290px;width:100%;height:140px;background:var(--white);
    display:flex;flex-direction:column;align-items:center;justify-content:center;font-family:"Montserrat",sans-serif;color:var(--ink);text-align:center}
  .caliber{font-weight:800;font-size:26px;line-height:1.1}
  .load-type{font-weight:700;font-size:11px;letter-spacing:.6px;margin-top:6px;line-height:1.4}

  /* back panel */
  .back-panel{position:absolute;left:184px;top:184px;width:860px;height:430px;overflow:hidden;
    background:linear-gradient(100deg,var(--red-deep) 0%,var(--red) 45%,#9a1518 70%,#6a0a0d 100%)}
  .back-header{position:absolute;inset:0;width:100%;height:100%}
  .back-panel .brand{position:absolute;left:440px;top:22px;font-size:30px}
  .warnings{position:absolute;left:44px;top:168px;width:780px;font-family:"Open Sans",sans-serif;font-size:12px;line-height:1.55;color:var(--text-light)}
  .warning-block + .warning-block{margin-top:22px}
  .warning-title{font-family:"Montserrat",sans-serif;font-weight:800;font-size:20px;color:var(--white);letter-spacing:.5px}
</style>
</head>
<body>
<main class="canvas">
  <section class="box-layout" aria-label="Crimson Ridge Arms ammunition box, flat panels">

    <header class="top-panel">
      <div class="brand"><span class="brand-dot"></span>Crimson Ridge Arms</div>
      <p class="product-line">FULL METAL JACKET<br>FMJ / ELITE AMMUNITION</p>
    </header>

    <aside class="end-panel">
      <div class="brand"><span class="brand-dot"></span>Crimson<br>Ridge Arms</div>
      <div class="end-chrome"></div>
      <div class="end-label">
        <p class="caliber">9mm 115gr</p>
        <p class="load-type">FULL METAL JACKET<br>FMJ / ELITE AMMUNITION</p>
      </div>
    </aside>

    <article class="back-panel">
      <svg class="back-header" viewBox="0 0 860 430" preserveAspectRatio="none" aria-hidden="true">
        <defs>
          <linearGradient id="chrome" x1="0" y1="0" x2="0" y2="1">
            <stop offset="0" stop-color="#dcdcdc"/>
            <stop offset=".55" stop-color="#6b6b6b"/>
            <stop offset="1" stop-color="#bdbdbd"/>
          </linearGradient>
        </defs>
        <polygon points="0,0 860,0 860,108 490,150 0,118" fill="url(#chrome)"/>
        <polygon points="0,0 860,0 860,86 490,128 0,96" fill="#ffffff"/>
      </svg>

      <div class="brand"><span class="brand-dot"></span>Crimson Ridge Arms</div>

      <div class="warnings">
        <p class="warning-block"><span class="warning-title">LEAD WARNING:</span> Discharging firearms in poorly ventilated areas, cleaning firearms, or handling ammunition may result in exposure to lead and other substances known to cause birth defects, reproductive harm, and other serious physical injury. Have adequate ventilation at all times. Wash hands thoroughly after exposure.</p>
        <p class="warning-block"><span class="warning-title">WARNING:</span> To avoid serious injury: (1) use only ammunition in good condition; use only in modern firearms in good condition marked for .22 Long Rifle (LR) cartridges; (2) always be sure barrel is free of any obstructions; the barrel should be checked in case of light recoil, or an unusually loud or weak sound heard during firing; (3) wear eye and ear protection; (4) if gun fails to fire, avoid exposure to breech when unloading and point muzzle in a safe direction. Keep firearm pointed in safe direction at all times; (5) discharge may occur if rim is struck; handle with caution, do not drop. (6) Do not shoot at hard surfaces or water to prevent ricochet; (7) Bullet is capable of traveling extreme distances. Know your backstop; (8) Store in cool dry place</p>
      </div>
    </article>

  </section>
</main>
</body>
</html>
```